BOLD & MINIMALIST DESIGN NEEDED

We want a very bold but minimalistic business card design that is impactful and utilizes both sides of the business card. Our current logo is included for your use.

We want bold fonts and good use of negative space. We don't want the logo to overpower the design.

Target Market(s)

Professionals who are building new commercial buildings.

Industry/Entity Type

Construction

Contact Information for Business Card

Name, Title, email, office phone, cell phone, website

Font styles to use
Serif
Sans Serif

Requirements
Must have
• Bold design!

```html
<!DOCTYPE html>
<html lang="en">
<head>
<meta charset="utf-8">
<title>Ridgeline Design + Build – Business Card</title>
<link href="https://fonts.googleapis.com/css2?family=Montserrat:wght@400;500;700;800;900&display=swap" rel="stylesheet">
<style>
  :root {
    --stage: #2c2c2c;
    --green: #86c440;
    --ink: #0c0c0d;
    --paper: #ffffff;
  }
  * { box-sizing: border-box; margin: 0; padding: 0; }
  html, body {
    width: 1200px; height: 689px; overflow: hidden;
    background: var(--stage);
    font-family: "Montserrat", Arial, sans-serif;
  }
  .canvas { position: relative; width: 1200px; height: 689px; }

  .card {
    position: absolute; top: 190px;
    width: 540px; height: 309px;
    border-radius: 22px; overflow: hidden;
  }

  /* Front side */
  .card-front {
    left: 40px;
    background: var(--green);
    display: flex; flex-direction: column; align-items: center; justify-content: center;
    color: var(--paper);
  }
  .front-name { display: flex; align-items: center; gap: 14px; }
  .brand-mark { width: 34px; height: 34px; background: var(--paper); }
  .front-wordmark { font-weight: 900; font-size: 58px; letter-spacing: 1px; line-height: 1; }
  .front-tagline { margin-top: 12px; font-weight: 500; font-size: 17px; letter-spacing: 9px; }

  /* Back side */
  .card-back { left: 620px; background: var(--paper); }
  .back-waves { position: absolute; inset: 0; width: 540px; height: 309px; }

  .back-brand {
    position: absolute; right: 34px; top: 30px; text-align: right; color: var(--ink);
  }
  .back-wordmark { font-weight: 900; font-size: 34px; line-height: 1; letter-spacing: .5px; }
  .back-tagline { margin-top: 8px; font-weight: 500; font-size: 10px; letter-spacing: 5px; }

  .accent-bar {
    position: absolute; left: 0; top: 78px; width: 9px; height: 46px; background: var(--green);
  }
  .person { position: absolute; left: 30px; top: 78px; }
  .person-name {
    font-weight: 800; font-size: 26px; color: var(--green); letter-spacing: .5px; line-height: 1.05;
  }
  .person-title {
    margin-top: 4px; font-weight: 400; font-size: 12px; color: var(--ink); letter-spacing: .8px;
  }

  .contact {
    position: absolute; left: 28px; top: 204px;
    list-style: none; color: var(--paper); font-size: 11.5px; line-height: 15px;
  }
  .contact li { display: flex; align-items: center; gap: 8px; }
  .contact .address { padding-left: 21px; margin-bottom: 4px; }
  .contact svg { width: 13px; height: 13px; flex: none; fill: var(--green); }
</style>
</head>
<body>
<main class="canvas">

  <section class="card card-front" aria-label="Card front">
    <div class="front-name">
      <span class="brand-mark"></span>
      <span class="front-wordmark">RIDGELINE</span>
    </div>
    <p class="front-tagline">DESIGN + BUILD</p>
  </section>

  <section class="card card-back" aria-label="Card back">
    <svg class="back-waves" viewBox="0 0 540 309" aria-hidden="true">
      <path d="M150,165 C280,126 420,112 540,106 L540,118 C420,126 290,140 150,165 Z" fill="var(--ink)"/>
      <path d="M0,172 C160,140 340,128 540,122 L540,134 C340,142 170,158 0,184 Z" fill="var(--green)"/>
      <path d="M0,190 C170,165 340,150 540,142 L540,309 L0,309 Z" fill="var(--ink)"/>
      <path d="M260,186 C360,166 450,157 540,152" stroke="var(--green)" stroke-width="1.5" fill="none"/>
    </svg>

    <div class="back-brand">
      <div class="back-wordmark">RIDGELINE</div>
      <div class="back-tagline">DESIGN + BUILD</div>
    </div>

    <span class="accent-bar"></span>
    <div class="person">
      <h1 class="person-name">MARCUS HALE</h1>
      <p class="person-title">OWNER-CEO</p>
    </div>

    <ul class="contact">
      <li class="address">Your address, City<br>State, Zip 1234</li>
      <li>
        <svg viewBox="0 0 16 16"><path d="M2 5c0-2 2-3 6-3s6 1 6 3v1h-3V5H5v1H2zM4 7h8l2 7H2z"/></svg>
        123 456 789
      </li>
      <li>
        <svg viewBox="0 0 16 16"><path d="M4 1h8v14H4zM5.5 3v9h5V3z"/></svg>
        123 456 789
      </li>
      <li>
        <svg viewBox="0 0 16 16"><path d="M1 3h14v10H1zM2.5 4.5 8 9l5.5-4.5"/></svg>
        info@yourmail.com
      </li>
      <li>
        <svg viewBox="0 0 16 16"><circle cx="8" cy="8" r="7"/></svg>
        www.yourwebsite.com
      </li>
    </ul>
  </section>

</main>
</body>
</html>
```